New business card/stationary for a consulting company

I am looking for a clean and very professional looking business card for my consulting company as well as corresponding stationary. I am uploading our logo. I like simple and powerful for the feel. No graphics but I am open on everything else. Below is my contact information but would like the final to be in a version I can add my employees information into and print. Thank you.

Daniel Whitcombe
dan@ferncliffadvisory.com
2870 North 9th Avenue, Summit Floor, Elm Ridge, Illinois 60531
www.ferncliffadvisory.com

Industry/Entity Type

Consulting

Contact Information for Business Card

Daniel Whitcombe
dan@ferncliffadvisory.com
www.ferncliffadvisory.com

Font styles to use
Serif
Sans Serif

Requirements
Must have
• Our logo and the business card details.
Nice to have
• our website www.ferncliffadvisory.com

```html
<!DOCTYPE html>
<html lang="en">
<head>
<meta charset="utf-8">
<title>Ferncliff Advisory — Business Card</title>
<link rel="stylesheet" href="https://fonts.googleapis.com/css2?family=Libre+Baskerville&family=Marcellus&family=Questrial&family=Source+Sans+3:wght@400;600&display=swap">
<style>
  :root {
    --backdrop: #3a3a3a;
    --paper: #f2f2f2;
    --navy: #03035f;
    --navy-faint: #14147a;
    --ink: #333333;
    --white: #ffffff;
  }
  * { margin: 0; padding: 0; box-sizing: border-box; }
  html, body { width: 1200px; height: 900px; overflow: hidden; }
  body { background: var(--backdrop); position: relative; }

  .card { position: absolute; top: 170px; width: 347px; height: 561px; overflow: hidden; }
  .card--front { left: 259px; background: var(--paper); }
  .card--back { left: 631px; background: var(--navy); }

  .front__brand {
    position: absolute; top: 308px; left: 0; width: 100%;
    top: 138px;
    display: flex; justify-content: center; align-items: center; gap: 10px;
    font-family: "Libre Baskerville", serif; font-size: 17px; letter-spacing: 1.5px;
    color: var(--navy);
  }
  .front__brand-mark { width: 12px; height: 12px; background: var(--navy); }

  .front__name {
    position: absolute; top: 349px; left: 0; width: 100%; text-align: center;
    font-family: "Marcellus", serif; font-size: 17.5px; letter-spacing: 1px; color: var(--navy);
  }
  .front__rule {
    position: absolute; top: 391px; left: 77px; width: 194px; height: 1px; background: var(--navy);
  }
  .front__address {
    position: absolute; top: 417px; left: 0; width: 100%; text-align: center;
    font-family: "Source Sans 3", sans-serif; font-size: 15px; line-height: 20px; color: var(--ink);
  }
  .front__contact {
    position: absolute; top: 485px; left: 0; width: 100%; text-align: center;
    font-family: "Source Sans 3", sans-serif; font-size: 15px; line-height: 20px; color: var(--ink);
  }
  .front__label { font-weight: 600; color: var(--navy); }
  .front__web { color: var(--navy); }

  .back__monogram {
    position: absolute; top: 196px; left: 0; width: 100%; text-align: center;
    font-family: "Libre Baskerville", serif; font-size: 120px; line-height: 1;
    color: var(--navy-faint); letter-spacing: 8px;
  }
  .back__block {
    position: absolute; left: 114px; top: 204px; width: 63px; height: 154px; background: var(--white);
  }
  .back__name {
    position: absolute; left: 219px; top: 280px; width: 440px;
    transform: translate(-50%, -50%) rotate(-90deg);
    text-align: center; white-space: nowrap;
    font-family: "Questrial", sans-serif; font-size: 33px; letter-spacing: 1.5px; color: var(--white);
  }
</style>
</head>
<body>
  <section class="card card--front">
    <div class="front__brand"><span class="front__brand-mark"></span>FERNCLIFF ADVISORY</div>
    <h1 class="front__name">DANIEL WHITCOMBE</h1>
    <div class="front__rule"></div>
    <p class="front__address">2870 North 9th Avenue,<br>Summit Floor, Elm Ridge,<br>Illinois 60531</p>
    <p class="front__contact"><span class="front__label">E:</span> dan@ferncliffadvisory.com<br><span class="front__web">www.ferncliffadvisory.com</span></p>
  </section>

  <section class="card card--back">
    <div class="back__monogram" aria-hidden="true">FA</div>
    <div class="back__block"></div>
    <div class="back__name">FERNCLIFF ADVISORY</div>
  </section>
</body>
</html>
```